National Mission Critical Construction Contractor needs Stationery Design to make a bold statement

We are a small commercial construction company, working primarily in mission critical facilities across the U.S.. We have exciting corporate changes going an and a new logo and office space so we need new stationery. The final design should incorporate our new logo and invoke a fresh, high-tech feel while looking simple and modern.

Industry/Entity Type

Construction

Contact Information for Business Card

We are required to list our state licensing qualifications on the back of our card.

Font styles to use
Sans Serif

Requirements
Must have
• We need to have a design for second page of stationery, envelopes both standard and with a window and for a 3 x 4 notepad.

```html
<!DOCTYPE html>
<html lang="en">
<head>
<meta charset="utf-8">
<title>Crestline Build Group – Stationery</title>
<link href="https://fonts.googleapis.com/css2?family=Source+Sans+3:wght@400;600&display=swap" rel="stylesheet">
<style>
:root{
  --stage:#a9a8a9;
  --paper:#f4f3f1;
  --white:#ffffff;
  --blue:#1a6fb8;
  --sky:#29a3df;
  --ink:#444444;
  --faint:#dfe6ee;
}
*{box-sizing:border-box;margin:0;padding:0}
html,body{width:1200px;height:754px;overflow:hidden}
body{background:var(--stage);font-family:"Source Sans 3",sans-serif;color:var(--ink);position:relative}
.sheet{position:absolute;box-shadow:0 1px 4px rgba(0,0,0,.25)}
.brand{font-weight:600;color:var(--blue);letter-spacing:.5px;text-align:center;line-height:1}
.brand-sub{display:block;font-size:.38em;letter-spacing:1.6px;margin-top:3px}
.dot{display:inline-block;border-radius:50%;border:2px solid var(--blue)}
.ring{position:absolute;border-radius:50%;border:10px solid var(--faint)}
.band-gradient{background:linear-gradient(90deg,var(--blue) 0%,var(--blue) 42%,var(--sky) 62%,var(--sky) 100%)}
.white-dot{position:absolute;border-radius:50%;background:var(--white);border:3px solid var(--blue)}

/* letterhead */
.letterhead{left:36px;top:32px;width:488px;height:688px;background:var(--paper);overflow:hidden}
.letterhead .ring{left:60px;top:224px;width:366px;height:366px;border-width:9px}
.letterhead .head{position:absolute;left:0;right:0;top:54px;font-size:20px}
.letterhead .head .dot{width:30px;height:30px;display:block;margin:0 auto 10px}
.salutation{position:absolute;left:49px;top:193px;font-size:13px;color:#333}
.body-copy{position:absolute;left:49px;top:232px;width:393px;font-size:7.6px;line-height:11.8px;text-align:justify}
.body-copy p{margin-bottom:11.8px}
.closing{position:absolute;left:49px;top:481px;font-size:7.5px}
.signature{position:absolute;left:47px;top:494px;width:66px;height:26px;background:#e6e6e6;border-radius:3px}
.signer{position:absolute;left:51px;top:534px;font-size:8px;line-height:13px}
.letterhead .footer{position:absolute;left:0;top:610px;width:488px;height:57px;color:var(--white);font-size:8.6px;line-height:11px}
.letterhead .footer .contacts{position:absolute;left:48px;top:8px}
.letterhead .footer .address{position:absolute;right:47px;top:8px;text-align:right}
.letterhead .footer .white-dot{left:216px;top:-1px;width:58px;height:58px}
.ico{display:inline-block;width:6px;height:6px;background:var(--white);margin-right:5px;border-radius:1px}

/* cards */
.card{width:214px;height:122px;background:var(--white)}
.card-front{left:649px;top:177px}
.card-front .brand{position:absolute;left:0;right:0;top:29px;font-size:13px}
.card-front .band{position:absolute;left:0;top:70px;width:214px;height:46px;color:var(--white)}
.card-front .who{position:absolute;left:9px;top:5px;font-size:5.6px;line-height:8px}
.card-front .who b{font-size:8px;font-weight:600;display:block;line-height:10px}
.card-front .lines{position:absolute;right:9px;top:6px;font-size:5.4px;line-height:8.2px;text-align:right}
.card-front .white-dot{left:84px;top:-1px;width:46px;height:46px;border-width:2px}
.card-back{left:894px;top:178px}
.card-back .brand{position:absolute;left:0;right:0;top:36px;font-size:13px}
.card-back .dot{width:24px;height:24px;display:block;margin:0 auto 8px}

/* envelopes */
.env-back{left:615px;top:360px;width:549px;height:250px;background:var(--paper)}
.flap{position:absolute;left:0;top:0;width:549px;height:92px}
.flap .site{position:absolute;left:0;right:0;top:62px;text-align:center;color:var(--white);font-size:8.6px}
.flap .mark{position:absolute;left:258px;top:24px;width:33px;height:33px;border-radius:50%;border:2px solid var(--white)}
.env-front{left:547px;top:470px;width:550px;height:250px;background:var(--paper);overflow:hidden}
.env-front .ring{left:301px;top:8px;width:250px;height:250px;border-width:5px}
.env-front .brand{position:absolute;left:29px;top:38px;font-size:12px;text-align:left;display:flex;align-items:center;gap:5px}
.env-front .brand .dot{width:26px;height:26px}
.env-front .band{position:absolute;left:0;top:210px;width:550px;height:19px;color:var(--white);font-size:8.5px;line-height:19px;padding-left:29px}
.env-front .band .white-dot{left:264px;top:-1px;width:21px;height:21px;border-width:2px}
</style>
</head>
<body>

<section class="sheet letterhead">
  <div class="ring" aria-hidden="true"></div>
  <div class="brand head"><span class="dot"></span>CRESTLINE BUILD<span class="brand-sub">GROUP</span></div>
  <p class="salutation">Dear Mr. Carter,</p>
  <div class="body-copy">
    <p>Lorem ipsum dolor sit amet, consectetur adipiscing elit. Donec orci purus, luctus vitae dignissim eu, iaculis sed purus. Vivamus faucibus, ipsum nec aliquet viverra, leo mauris condimentum ligula, sit amet sagittis enim ligula quis arcu. Nam egestas tortor id nisi porttitor mattis. In tortor ante, ultricies in suscipit a, tempus non massa. Vivamus et auctor mi. Fusce vel massa nulla. Phasellus nec eros mauris, et scelerisque orci.</p>
    <p>Donec malesuada orci vitae nulla accumsan porta a id massa. Quisque accumsan iaculis magna sit amet fringilla. Maecenas consequat, magna eget tincidunt semper, odio nibh rutrum mi, id feugiat ante nisi eu risus. Vestibulum nunc orci, rhoncus a placerat in, ultricies in mi. Cras mattis varius eros, vel fringilla nisi suscipit eget. Quisque scelerisque sagittis nulla at porttitor.</p>
    <p>Sed id augue vitae urna euismod commodo aliquet a quam. Pellentesque arcu velit, cursus et malesuada ut, consequat et diam. Nullam erat sem, rhoncus id ullamcorper vitae, rhoncus et arcu. In ultricies ultricies nulla, ut rutrum nisi iaculis at. Donec eu magna a metus ornare faucibus. Fusce aliquet faucibus ultricies. Morbi semper, est id tincidunt gravida, sem arcu adipiscing lacus, ac bibendum nulla leo eu purus. Quisque nec diam sed risus consectetur a accumsan quis quis nibh. Vestibulum id purus lorem.</p>
    <p>It is a long established fact that a reader will be distracted by the readable content of a page when looking at its layout. The point of using Lorem Ipsum is that it has a more-or-less normal distribution of letters, as opposed to using 'Content here, content here', making it look like readable English. Many desktop publishing packages</p>
  </div>
  <p class="closing">Sincerely,</p>
  <div class="signature" role="img" aria-label="Handwritten signature"></div>
  <p class="signer">Daniel Reyes<br>CEO/ Founder</p>
  <div class="footer band-gradient">
    <div class="contacts"><span class="ico"></span>555 214 7093<br><span class="ico"></span>555 386 1420<br><span class="ico"></span>555 902 6618<br><span class="ico"></span>hello@crestlinebuild.com</div>
    <div class="white-dot" aria-hidden="true"></div>
    <div class="address">1420 Harbor Street<br>Fairbanks<br>Alaska 99701<br>www.crestlinebuild.com</div>
  </div>
</section>

<section class="sheet card card-front">
  <div class="brand">CRESTLINE BUILD<span class="brand-sub">GROUP</span></div>
  <div class="band band-gradient">
    <div class="who"><b>DANIEL REYES</b>CEO/Founder<br>1420 Harbor Street<br>Fairbanks, Alaska 99701</div>
    <div class="white-dot" aria-hidden="true"></div>
    <div class="lines">555 214 7093<br>555 386 1420<br>555 902 6618<br>hello@crestlinebuild.com</div>
  </div>
</section>

<section class="sheet card card-back">
  <div class="brand"><span class="dot"></span>CRESTLINE BUILD<span class="brand-sub">GROUP</span></div>
</section>

<section class="sheet env-back">
  <svg class="flap" viewBox="0 0 549 92" aria-hidden="true">
    <path d="M0 0H549L540 45Q533 92 490 92H58Q18 92 10 50Z" fill="var(--blue)"/>
  </svg>
  <div class="flap">
    <div class="mark"></div>
    <p class="site">www.crestlinebuild.com</p>
  </div>
</section>

<section class="sheet env-front">
  <div class="ring" aria-hidden="true"></div>
  <div class="brand"><span class="dot"></span><span>CRESTLINE BUILD<span class="brand-sub">GROUP</span></span></div>
  <div class="band band-gradient">1420 Harbor Street, Fairbanks, Alaska 99701<div class="white-dot" aria-hidden="true"></div></div>
</section>

</body>
</html>
```